Business card for my new company (Accounting firm)

I need a business card for my new business Brightwell Advisory and Ledger SA. Our services are accounting, tax, audit and financial management. Our customers are small companies, start-ups and new companies. The final design has to show financial security, trust and growth. Please find our logo attached to the business card. Text for the business card: Brightwell Advisory and Ledger SA Tomas Varenholt Director and Founder Certified Accountant Tel. 022 418 57 34 tv@clairevalconseil.ch www.clairevalconseil.ch Rue des Vergières 27 1201 Geneva
Target Market(s)
Our customers are small companies, start-ups and new companies.
Industry/Entity Type
Finance And Accounting
Contact Information for Business Card
Claireval Conseil et Comptes SA
Tomas Varenholt
Directeur et Fondateur
Expert-comptable diplômé
Tél. 022 418 57 34
tv@clairevalconseil.ch
www.clairevalconseil.ch
Rue des Vergières 27
1201 Genève

```html
<!DOCTYPE html>
<html lang="fr">
<head>
<meta charset="utf-8">
<title>Claireval Conseil et Comptes SA — Carte de visite</title>
<link rel="stylesheet" href="https://fonts.googleapis.com/css2?family=Montserrat:wght@300;400;500;700&display=swap">
<style>
  :root {
    --backdrop: #c9cacc;
    --paper: #ffffff;
    --brand-blue: #29a9e1;
    --brand-blue-deep: #1b6fae;
    --pattern-blue: #2aa3dc;
    --ink-dark: #2c2c2e;
    --ink-grey: #6b6b6e;
  }
  * { box-sizing: border-box; margin: 0; padding: 0; }
  html, body {
    width: 1200px;
    height: 801px;
    overflow: hidden;
    background: var(--backdrop);
    font-family: "Montserrat", sans-serif;
  }
  .sheet {
    width: 1200px;
    height: 801px;
    display: flex;
    align-items: center;
    justify-content: center;
    gap: 40px;
  }
  .card {
    width: 540px;
    height: 309px;
    position: relative;
    overflow: hidden;
    box-shadow: 0 6px 18px rgba(0, 0, 0, 0.18);
  }
  /* Front side */
  .card-front {
    background: var(--paper);
  }
  .wordmark {
    position: absolute;
    top: 42px;
    right: 40px;
    display: flex;
    align-items: center;
    gap: 10px;
  }
  .wordmark-square {
    width: 30px;
    height: 30px;
    background: var(--brand-blue-deep);
  }
  .wordmark-name {
    font-weight: 700;
    font-size: 30px;
    letter-spacing: 2px;
    color: var(--ink-dark);
    text-transform: uppercase;
  }
  .contact-block {
    position: absolute;
    left: 36px;
    bottom: 30px;
  }
  .person-name {
    font-weight: 400;
    font-size: 27px;
    color: var(--brand-blue);
    line-height: 1.1;
  }
  .person-role {
    font-weight: 500;
    font-size: 16px;
    color: var(--ink-dark);
    line-height: 1.3;
  }
  .address {
    margin-top: 10px;
    font-weight: 300;
    font-size: 14px;
    color: var(--ink-grey);
  }
  .contact-line {
    margin-top: 4px;
    font-weight: 300;
    font-size: 12.5px;
    color: var(--ink-grey);
    white-space: nowrap;
  }
  .contact-line b {
    font-weight: 700;
    color: var(--ink-dark);
  }
  /* Back side */
  .card-back {
    background: var(--pattern-blue);
  }
  .back-pattern {
    position: absolute;
    inset: 0;
    background: linear-gradient(135deg, #35b4ea 0%, #2aa3dc 55%, #2196d2 100%);
  }
  .back-name {
    position: absolute;
    right: 36px;
    bottom: 118px;
    font-weight: 700;
    font-size: 18px;
    letter-spacing: 2px;
    color: var(--paper);
    text-transform: uppercase;
  }
</style>
</head>
<body>
  <main class="sheet">
    <section class="card card-front" aria-label="Recto de la carte">
      <div class="wordmark">
        <span class="wordmark-square"></span>
        <span class="wordmark-name">Claireval</span>
      </div>
      <div class="contact-block">
        <p class="person-name">Tomas Varenholt</p>
        <p class="person-role">Directeur et Fondateur</p>
        <p class="person-role">Expert-comptable diplômé</p>
        <p class="address">Rue des Vergières 27 1201 Genève</p>
        <p class="contact-line"><b>P.</b> 022 418 57 34 <b>E.</b> tv@clairevalconseil.ch <b>W.</b> clairevalconseil.ch</p>
      </div>
    </section>
    <section class="card card-back" aria-label="Verso de la carte">
      <div class="back-pattern" role="img" aria-label="Motif répété du symbole de la marque en bleu ton sur ton"></div>
      <span class="back-name">Claireval</span>
    </section>
  </main>
</body>
</html>
```